full stationary design for a modern sleek design company

we are a design company that does modern minimalistic interior design works as well as other design services for high end clients.
we need a full stationary design including and not limited to (double sided business card, letter head, envelopes, documents folder...etc) that reflects the modern style design we do.
sleek modern and minimalistic is the requirements.
Updates

please use the latest attached files as there was a slight modification on the logo Added Wednesday, March 1, 2017

minor update on the logo files in JPG and PSD has been updated kindly follow the new attachments. Added Thursday, March 2, 2017

Target Market(s)

modern minimalist clients

Industry/Entity Type

Design Agency

Requirements
Must have
• the logo
Nice to have
• i like the colors in the colored 3D logo attached
Should not have
• too many colors

```html
<!DOCTYPE html>
<html lang="en">
<head>
<meta charset="utf-8">
<title>Lumen Atelier – Business Card</title>
<link rel="stylesheet" href="https://fonts.googleapis.com/css2?family=Open+Sans:wght@400;700&display=swap">
<style>
  :root {
    --backdrop: #e7e4df;
    --charcoal: #333536;
    --orange: #f7941d;
    --paper: #ffffff;
    --ink-light: #f2f2f2;
    --card-w: 616px;
    --card-h: 351px;
  }
  * { box-sizing: border-box; margin: 0; padding: 0; }
  html, body {
    width: 1200px;
    height: 987px;
    overflow: hidden;
  }
  body {
    background: var(--backdrop);
    font-family: "Open Sans", Arial, sans-serif;
    position: relative;
  }
  .card {
    position: absolute;
    left: 292px;
    width: var(--card-w);
    height: var(--card-h);
  }
  .card-front { top: 130px; }
  .card-back { top: 506px; }
  .card-shape {
    position: absolute;
    inset: 0;
    width: 100%;
    height: 100%;
  }

  .contact {
    position: absolute;
    left: 36px;
    top: 64px;
    color: var(--ink-light);
  }
  .contact-name {
    color: var(--orange);
    font-weight: 700;
    font-size: 21px;
    line-height: 26px;
    letter-spacing: 0.2px;
  }
  .contact-title {
    font-size: 16px;
    line-height: 22px;
  }
  .contact-address {
    margin-top: 13px;
    font-size: 15.5px;
    line-height: 23px;
  }
  .contact-lines {
    list-style: none;
    margin-top: 4px;
  }
  .contact-lines li {
    display: flex;
    align-items: center;
    gap: 8px;
    font-size: 15.5px;
    line-height: 23.5px;
  }
  .contact-icon {
    width: 14px;
    height: 14px;
    flex: none;
  }

  .brand {
    position: absolute;
    display: flex;
    align-items: center;
    gap: 10px;
    font-weight: 700;
    letter-spacing: 2.5px;
    white-space: nowrap;
  }
  .brand-mark {
    background: var(--orange);
    flex: none;
  }
  .brand-front {
    left: 318px;
    top: 160px;
    color: var(--charcoal);
    font-size: 22px;
  }
  .brand-front .brand-mark { width: 22px; height: 22px; }
  .brand-back {
    left: 50%;
    top: 50%;
    transform: translate(-50%, -50%);
    color: var(--ink-light);
    font-size: 34px;
  }
  .brand-back .brand-mark { width: 34px; height: 34px; }
</style>
</head>
<body>

  <section class="card card-front" aria-label="Business card front">
    <svg class="card-shape" viewBox="0 0 616 351" aria-hidden="true">
      <path d="M47 0 H616 V351 H0 V47 A47 47 0 0 1 47 0 Z" fill="var(--charcoal)"/>
      <clipPath id="front-clip"><rect width="616" height="351"/></clipPath>
      <g clip-path="url(#front-clip)">
        <path d="M446 -4 A180 180 0 0 0 446 356 H616 V-4 Z" fill="var(--paper)"/>
        <path d="M446 -6 A182 182 0 0 0 446 358" fill="none" stroke="var(--orange)" stroke-width="5"/>
      </g>
    </svg>

    <div class="contact">
      <p class="contact-name">MARC DELAUNAY</p>
      <p class="contact-title">CEO&amp;Founder</p>
      <p class="contact-address">214 Willow Crest Road<br>Fairview, Oregon 97024</p>
      <ul class="contact-lines">
        <li>
          <svg class="contact-icon" viewBox="0 0 14 14" aria-hidden="true"><path d="M3 1 L5.2 3.6 L4 5.2 C5 7.3 6.7 9 8.8 10 L10.4 8.8 L13 11 L11.4 13 C6 12.6 1.4 8 1 2.6 Z" fill="var(--orange)"/></svg>
          (555) 310 4826
        </li>
        <li>
          <svg class="contact-icon" viewBox="0 0 14 14" aria-hidden="true"><rect x="3.5" y="0.5" width="7" height="13" rx="1.3" fill="none" stroke="var(--orange)" stroke-width="1.6"/><circle cx="7" cy="11.2" r="0.9" fill="var(--orange)"/></svg>
          (555) 702 1957
        </li>
        <li>
          <svg class="contact-icon" viewBox="0 0 14 14" aria-hidden="true"><rect x="0.5" y="3" width="13" height="8.5" fill="var(--orange)"/><path d="M0.5 3 L7 8 L13.5 3" fill="none" stroke="var(--charcoal)" stroke-width="1.1"/></svg>
          marc@lumenatelier.com
        </li>
        <li>
          <svg class="contact-icon" viewBox="0 0 14 14" aria-hidden="true"><circle cx="7" cy="7" r="6.3" fill="var(--orange)"/><path d="M3 4 C5 5 4 7 6 8 C7 9 5 11 6 13 M9 1.5 C8.5 3.5 10.5 4 11.5 6" fill="none" stroke="var(--charcoal)" stroke-width="1.2"/></svg>
          www.lumenatelier.com
        </li>
      </ul>
    </div>

    <div class="brand brand-front">
      <span class="brand-mark" aria-hidden="true"></span>
      <span class="brand-name">LUMEN ATELIER</span>
    </div>
  </section>

  <section class="card card-back" aria-label="Business card back">
    <svg class="card-shape" viewBox="0 0 616 351" aria-hidden="true">
      <path d="M0 0 H569 A47 47 0 0 1 616 47 V351 H0 Z" fill="var(--charcoal)"/>
    </svg>
    <div class="brand brand-back">
      <span class="brand-mark" aria-hidden="true"></span>
      <span class="brand-name">LUMEN ATELIER</span>
    </div>
  </section>

</body>
</html>
```